Hartwell Estates Business Cards

I would like a business card that includes myself and my partner.
Includes: Logo, office #, email, website, our names, our numbers and possibly the address. I would also like the logo to be embossed and the card to be horizontal.
There is a photo of our yard signs to give you an idea of the colors of our business.

Target Market(s)

Everyone in real estate market.
We are in a rural area. Our clientele are from all socioeconomic backgrounds.

Industry/Entity Type

Real Estate Agent

Contact Information for Business Card

Company Name: Hartwell Estates
Our Names, Titles & Cell #'s : Dana Pembrook-Broker (555).317.6624, Marla Pembrook-Realtor (555).609.1385
Office #: (555).240.3918
Website: hartwellestates-demo.com
Joint Email: pembrook@hartwellestates-demo.com
Office Address: 418B W. Calloway Ave.
Larkfield, KS. 70913

Font styles to use
Serif

Requirements
Must have
• HORIZONTAL, Logo, Myself and my partners names, Our cell #'s, our office #, our website, our email address
Nice to have
• Embossed logo, office address, our titles.

```html
<!DOCTYPE html>
<html lang="en">
<head>
<meta charset="utf-8">
<title>Hartwell Estates Business Cards</title>
<link href="https://fonts.googleapis.com/css2?family=Cinzel:wght@400&family=Mulish:wght@400;600;700&display=swap" rel="stylesheet">
<style>
  :root {
    --purple: #5b1a8c;
    --purple-deep: #45106e;
    --purple-emboss: #7231a6;
    --taupe: #7a735f;
    --paper: #fbfbfa;
    --ink: #5a1a8a;
    --backdrop: #e9e6e1;
  }
  html, body {
    margin: 0;
    width: 1200px;
    height: 1022px;
    overflow: hidden;
    background: var(--backdrop);
  }
  .canvas {
    position: relative;
    width: 1200px;
    height: 1022px;
  }
  .card {
    position: absolute;
    left: 250px;
    width: 700px;
    height: 400px;
    border-radius: 14px;
    overflow: hidden;
    box-shadow: 0 8px 24px rgba(0,0,0,0.18);
  }
  .card-front {
    top: 91px;
    background: linear-gradient(135deg, var(--purple-deep) 0%, var(--purple) 55%, #6a2a9c 100%);
  }
  .brand {
    position: absolute;
    left: 0;
    right: 0;
    top: 50%;
    transform: translateY(-50%);
    display: flex;
    align-items: center;
    justify-content: center;
    gap: 22px;
  }
  .brand-dot {
    width: 54px;
    height: 54px;
    border-radius: 50%;
    background: var(--purple-emboss);
  }
  .brand-name {
    font-family: "Cinzel", serif;
    font-weight: 400;
    font-size: 54px;
    letter-spacing: 3px;
    color: var(--purple-emboss);
  }
  .card-back {
    top: 531px;
    background: var(--paper);
  }
  .back-band {
    position: absolute;
    inset: 0;
  }
  .contact {
    position: absolute;
    right: 40px;
    top: 34px;
    text-align: right;
    font-family: "Mulish", sans-serif;
    color: var(--ink);
  }
  .person { margin-bottom: 10px; }
  .person-name {
    font-weight: 700;
    font-size: 27px;
    line-height: 32px;
  }
  .person-title, .person-phone, .office-line {
    font-size: 16px;
    line-height: 21px;
  }
  .office { margin-top: 12px; }
  .office-line {
    display: flex;
    justify-content: flex-end;
    align-items: center;
    gap: 8px;
  }
  .office-line .icon {
    width: 13px;
    height: 13px;
    fill: none;
    stroke: var(--ink);
    stroke-width: 1.6;
  }
  .web strong { font-weight: 700; }
</style>
</head>
<body>
<main class="canvas">

  <section class="card card-front" aria-label="Card front">
    <div class="brand">
      <span class="brand-dot"></span>
      <span class="brand-name">Hartwell Estates</span>
    </div>
  </section>

  <section class="card card-back" aria-label="Card back">
    <svg class="back-band" viewBox="0 0 700 400" preserveAspectRatio="none" aria-hidden="true">
      <path d="M0 0 H300 C220 120 200 260 255 400 H0 Z" fill="var(--purple)"/>
      <path d="M300 0 C220 120 200 260 255 400" fill="none" stroke="var(--taupe)" stroke-width="14"/>
      <path d="M310 0 C230 120 210 260 265 400" fill="none" stroke="#ffffff" stroke-width="3"/>
    </svg>

    <div class="contact">
      <div class="person">
        <div class="person-name">Dana Pembrook</div>
        <div class="person-title">Broker</div>
        <div class="person-phone">(555).317.6624</div>
      </div>
      <div class="person">
        <div class="person-name">Marla Pembrook</div>
        <div class="person-title">Realtor</div>
        <div class="person-phone">(555).609.1385</div>
      </div>
      <div class="office">
        <div class="office-line"><span>418B W. Calloway Ave.</span></div>
        <div class="office-line"><span>Larkfield, KS. 70913</span></div>
        <div class="office-line"><span>(555).240.3918</span>
          <svg class="icon" viewBox="0 0 16 16" aria-hidden="true"><path d="M4 1.5 L6.5 5 L5 6.5 C6 8.5 7.5 10 9.5 11 L11 9.5 L14.5 12 L12.5 14.5 C7 14 2 9 1.5 3.5 Z"/></svg>
        </div>
        <div class="office-line"><span>pembrook@hartwellestates-demo.com</span>
          <svg class="icon" viewBox="0 0 16 16" aria-hidden="true"><rect x="1.5" y="3.5" width="13" height="9"/><path d="M1.5 3.5 L8 9 L14.5 3.5"/></svg>
        </div>
        <div class="office-line web"><span>www.<strong>hartwellestates-demo.com</strong></span>
          <svg class="icon" viewBox="0 0 16 16" aria-hidden="true"><circle cx="8" cy="8" r="6.5"/><ellipse cx="8" cy="8" rx="3" ry="6.5"/><path d="M1.5 8 H14.5"/></svg>
        </div>
      </div>
    </div>
  </section>

</main>
</body>
</html>
```